Motivational Poster Design Project

I would like to create a poster with some of my favorite quotes to hang in my office. I did a similar project in 2012 and I've uploaded the top 2 designs so you can get a better idea of what I'm looking for. I will provide feedback on your design within 24 hours of receiving it.

The poster must contain the following quotes:

"You’re only given a little spark of madness. You mustn’t lose it.”
- Dorian Fletcher

“The most contrarian thing of all is not to oppose the crowd but to think for yourself.”
- Marcus Olden

"I constantly see people rise in life who are not the smartest, sometimes not even the most diligent, but they are learning machines. They go to bed every night a little wiser than they were when they got up and boy does that help, particularly when you have a long run ahead of you."
- Frankie Dalgarth

“In theory, there’s no difference between theory and practice. But, in practice, there is.”
- Kees R. T. Ter Haverkamp

"At the end of the day, a reactionary life is a normal life. One thing is consistent in every remarkable person: they decide to do something remarkable. Don’t let the world choose who you become."
- Rohan Kapadia

“It usually takes 3-4 months to try enough that you can do a proper 80/20 analysis, then two months to design systems to scale what *is* working.”
-Ned Yarrow

“Authority is 20 percent given, 80 percent taken.”
- Glenn Mosbacker

“Your actions are consistent with the way the world occurs to you.”
- Dieter Kolbach

Project Deadline Extended
Reason: I am going to be travelling with no access to internet until January 5th, 2015. I am extending the project deadline until 12/31/14 and I'll make a final decision during the 1st week of January.

Target Market(s)

Personal Project

Industry/Entity Type

Learning

Requirements
Must have
• The poster will be 24" high x 36" long and printed on canvas, so the image you create needs to have a resolution of at least 2700 x 3900.
Nice to have
• I don't have an exact vision for how the poster should look, so I am totally open to you using your creativity to develop, arrange and present the content as you'd like.
• That said, I would like an image (photo or posterized image) of the person being quoted along with each quote. I do not have specific images that I would like you to use, so you will need to find the images on your own. The images don't need to be perfect... I am more interested in the poster relating the essence of the quotes and the people being quoted than I am in perfect photographic images of the people being quoted.

```html
<!DOCTYPE html>
<html lang="en">
<head>
<meta charset="utf-8">
<title>Quote Board</title>
<link rel="stylesheet" href="https://fonts.googleapis.com/css2?family=Open+Sans:wght@400;600;700&family=Alegreya:ital,wght@1,700&display=swap">
<style>
  :root {
    --cork-light: #8a6a3e;
    --cork-mid: #6a4c27;
    --cork-dark: #1c120a;
    --frame-light: #ecebe6;
    --frame-mid: #cfcdc6;
    --frame-edge: #a9a59c;
    --square-black: #0b0b0b;
    --ink-name: #1b1a18;
    --pin-green: #6d8c45;
    --pin-dark: #3f5624;
    --quote-stone: #c9c4aa;
    --quote-gold: #dcc88e;
    --quote-grey: #a9a9a9;
    --quote-white: #f2f2f2;
    --quote-salmon: #e79c82;
    --quote-orange: #e2936a;
    --quote-pink: #eb9fa6;
    --quote-sage: #b7d09c;
    --portrait-light: #77726a;
    --portrait-dark: #34312d;
  }
  * { box-sizing: border-box; margin: 0; padding: 0; }
  html, body { width: 1200px; height: 800px; overflow: hidden; }
  body {
    position: relative;
    font-family: "Open Sans", sans-serif;
    background:
      radial-gradient(ellipse 75% 70% at 50% 45%, var(--cork-light) 0%, var(--cork-mid) 55%, var(--cork-dark) 100%);
  }
  .card {
    position: absolute;
    width: 268px;
    height: 330px;
    padding: 16px 16px 0;
    background: linear-gradient(160deg, var(--frame-light) 0%, var(--frame-mid) 60%, var(--frame-edge) 100%);
    box-shadow: 3px 6px 12px rgba(0,0,0,0.6), inset 0 0 18px rgba(90,75,50,0.35);
  }
  .pin {
    position: absolute;
    top: -8px; left: 50%;
    width: 18px; height: 18px;
    margin-left: -9px;
    border-radius: 50%;
    background: radial-gradient(circle at 35% 30%, #a7c27b 0%, var(--pin-green) 45%, var(--pin-dark) 100%);
    box-shadow: 2px 4px 4px rgba(0,0,0,0.55);
  }
  .square {
    position: relative;
    width: 236px; height: 236px;
    background: var(--square-black);
    overflow: hidden;
  }
  .portrait {
    position: absolute;
    bottom: 0;
    background: radial-gradient(ellipse 55% 60% at 50% 45%, var(--portrait-light) 0%, var(--portrait-dark) 55%, transparent 80%);
    opacity: 0.85;
  }
  .quote {
    position: relative;
    z-index: 1;
    padding: 22px 18px;
    line-height: 1.35;
  }
  .quote b { font-weight: 700; }
  .name {
    height: 78px;
    display: flex; align-items: center; justify-content: center;
    text-align: center;
    font-family: "Alegreya", serif;
    font-style: italic; font-weight: 700;
    font-size: 25px; line-height: 1.05;
    color: var(--ink-name);
  }
  .name.long { font-size: 22px; }

  .r1 { top: 52px; } .r2 { top: 412px; }
  .c1 { left: 28px; } .c2 { left: 322px; } .c3 { left: 610px; } .c4 { left: 904px; }

  .q-spark { color: var(--quote-stone); font-size: 19px; padding-top: 34px; padding-left: 24px; }
  .q-spark b { font-size: 25px; }
  .q-contrarian { color: var(--quote-stone); font-size: 16px; padding-top: 34px; }
  .q-contrarian b { color: var(--quote-gold); font-size: 18px; }
  .q-learning { color: var(--quote-grey); font-size: 10.5px; padding: 16px 14px; line-height: 1.55; }
  .q-learning b { color: var(--quote-white); font-size: 13px; }
  .q-theory { color: var(--quote-salmon); font-size: 15px; padding-top: 28px; }
  .q-theory b { font-size: 20px; }
  .q-remarkable { color: var(--quote-grey); font-size: 11.5px; padding: 24px 14px; line-height: 1.55; }
  .q-remarkable b { color: var(--quote-white); font-size: 14px; }
  .q-analysis { color: var(--quote-orange); font-size: 12.5px; padding-top: 28px; line-height: 1.6; }
  .q-analysis b { font-size: 15px; }
  .q-authority { color: var(--quote-pink); font-size: 22px; padding-top: 24px; line-height: 1.5; }
  .q-authority b { font-size: 24px; }
  .q-actions { color: var(--quote-sage); font-size: 18px; padding-top: 26px; line-height: 1.6; }
  .q-actions b { font-size: 20px; }
</style>
</head>
<body>

<article class="card r1 c1">
  <span class="pin"></span>
  <div class="square">
    <div class="portrait" style="left:6px;width:100px;height:140px" role="img" aria-label="Black and white portrait of Dorian Fletcher"></div>
    <p class="quote q-spark">"You're only given a <b>little spark</b> of <b>madness</b>. You mustn't <b>lose</b> it."</p>
  </div>
  <div class="name">Dorian Fletcher</div>
</article>

<article class="card r1 c2">
  <span class="pin"></span>
  <div class="square">
    <div class="portrait" style="left:8px;width:110px;height:130px" role="img" aria-label="Black and white photo of Marcus Olden speaking at a lectern"></div>
    <p class="quote q-contrarian">"The <b>most contrarian thing</b> of all is <b>not to oppose</b> the crowd but <b>to think</b> for <b>yourself</b>."</p>
  </div>
  <div class="name">Marcus Olden</div>
</article>

<article class="card r1 c3">
  <span class="pin"></span>
  <div class="square">
    <div class="portrait" style="right:0;width:110px;height:110px" role="img" aria-label="Black and white portrait of Frankie Dalgarth"></div>
    <p class="quote q-learning">"I constantly see people rise in life who are not <b>the smartest</b>, sometimes not even <b>the most diligent</b>, but they are <b>learning machines</b>. They <b>go to bed</b> every night a little wiser than they were when they <b>got up</b> and boy does that help, particularly when you have a <b>long run</b> ahead of you."</p>
  </div>
  <div class="name">Frankie Dalgarth</div>
</article>

<article class="card r1 c4">
  <span class="pin"></span>
  <div class="square">
    <div class="portrait" style="right:0;width:110px;height:150px" role="img" aria-label="Black and white portrait of Kees R. T. Ter Haverkamp"></div>
    <p class="quote q-theory">"In theory, there's <b>no difference</b> between <b>theory</b> and <b>practice</b>. But, <b>in practice</b>, <b>there is</b>."</p>
  </div>
  <div class="name long">Kees R. T. Ter<br>Haverkamp</div>
</article>

<article class="card r2 c1">
  <span class="pin"></span>
  <div class="square">
    <div class="portrait" style="left:6px;width:90px;height:110px" role="img" aria-label="Black and white portrait of Rohan Kapadia"></div>
    <p class="quote q-remarkable">"At the end of the day, a <b>reactionary life</b> is a <b>normal life</b>. One thing is <b>consistent</b> in every <b>remarkable person</b>: they <b>decide to do</b> something remarkable. <b>Don't let the world choose</b> who you become."</p>
  </div>
  <div class="name">Rohan Kapadia</div>
</article>

<article class="card r2 c2">
  <span class="pin"></span>
  <div class="square">
    <div class="portrait" style="right:8px;width:100px;height:120px" role="img" aria-label="Black and white portrait of Ned Yarrow"></div>
    <p class="quote q-analysis">"It usually takes <b>3-4 months</b> to <b>try enough</b> that you can do a <b>proper 80/20 analysis</b>, then two months to <b>design</b> systems to <b>scale</b> what <b>*is* working</b>."</p>
  </div>
  <div class="name">Ned Yarrow</div>
</article>

<article class="card r2 c3">
  <span class="pin"></span>
  <div class="square">
    <div class="portrait" style="left:60px;width:120px;height:120px" role="img" aria-label="Black and white photo of Glenn Mosbacker gesturing while speaking"></div>
    <p class="quote q-authority">"Authority is<br><b>20 percent given,</b><br><b>80 percent</b><br><b>taken</b>."</p>
  </div>
  <div class="name">Glenn Mosbacker</div>
</article>

<article class="card r2 c4">
  <span class="pin"></span>
  <div class="square">
    <div class="portrait" style="right:8px;width:120px;height:160px" role="img" aria-label="Black and white photo of Dieter Kolbach on stage"></div>
    <p class="quote q-actions">"Your <b>actions</b> are <b>consistent</b> with the way the world <b>occurs to you</b>."</p>
  </div>
  <div class="name">Dieter Kolbach</div>
</article>

</body>
</html>
```